I need a flyer made , the flyer can be one page or two pages or three pages . I will be posting this on Instagram and social media platforms. I am a luxury home builder , I am looking to hire a construction project manager . Below are some examples and ideas what can be on the flyer

We’re looking for a construction project manager who’s passionate about building luxury homes at the highest standards
We’re hiring construction project manager
* Experience 5+ years in residential project management with a strong portfolio of completed homes.
* location : Bergen County NJ
* excellent leadership skills, leads teams with confidence and clarity
* communicates seamlessly with architects , engineers, designers and clients
*knows how to manage budgets and timelines without compromising quality
*solves problems with a positive solution first mindset
* pays attention to every detail because in luxury the small things are the big things

Apply now , link in bio or DM to connect.

My logo is attached, my web site www.velstridebuilders.com
My style is modern but still warm and inviting. I like a clean classy look .

Please don’t add any images of chairs or people to the flyer , I do not want people on my flyer. Do not add standard images of offices and houses , we are luxury builders , we build homes over 2 million dollars. Keep a classy , simple modern look . High end .

You can add a white hard hat with my logo on it for a image , this is a suggestion does not have to be on my flyer ,

```html
<!DOCTYPE html>
<html lang="en">
<head>
<meta charset="utf-8">
<title>Velstride Builders – Construction Project Manager</title>
<link href="https://fonts.googleapis.com/css2?family=Montserrat:ital,wght@0,400;0,500;0,600;0,700;0,800;1,500;1,700&display=swap" rel="stylesheet">
<style>
  :root {
    --ink: #0c0c0e;
    --gold: #77623f;
    --gold-band: #6a5a3d;
    --silver: #a3a9b9;
    --silver-light: #c4c8d2;
    --white: #ffffff;
    --rule: #3a3a3e;
    --panel-rule: #7f8596;
    --text-dark: #16161a;
  }
  * { margin: 0; padding: 0; box-sizing: border-box; }
  html, body { width: 1200px; height: 1200px; overflow: hidden; background: var(--ink); }
  .flyer {
    position: relative; width: 1200px; height: 1200px; overflow: hidden;
    font-family: "Montserrat", sans-serif; color: var(--silver);
    background: var(--ink);
  }
  .blueprint-backdrop {
    position: absolute; inset: 0;
    background: radial-gradient(ellipse at 60% 35%, #232326 0%, #141416 45%, #0b0b0d 80%);
  }
  .abs { position: absolute; white-space: nowrap; }

  .headline-were { left: 469px; top: 88px; font-size: 60px; font-weight: 700; letter-spacing: 9px; color: var(--gold); line-height: 1; }
  .headline-hiring { left: 76px; top: 94px; font-size: 212px; font-weight: 700; letter-spacing: -4px; line-height: 1; }
  .role-kicker { left: 83px; top: 316px; font-size: 39px; font-weight: 500; letter-spacing: 4.3px; color: var(--silver-light); line-height: 1; }
  .role-title { left: 80px; top: 369px; font-size: 107px; font-weight: 700; color: var(--gold); line-height: 86px; letter-spacing: -1px; }

  .brand { left: 824px; top: 120px; width: 270px; text-align: center; color: var(--white); font-weight: 500; }
  .brand-name { font-size: 41px; letter-spacing: 3px; line-height: 1; }
  .brand-sub { font-size: 15px; letter-spacing: 3px; line-height: 1; margin-top: 12px; }

  .exp-number { left: 811px; top: 379px; font-size: 107px; font-weight: 800; color: var(--gold); line-height: 1; letter-spacing: -3px; }
  .exp-years { left: 968px; top: 429px; font-size: 44px; font-weight: 800; line-height: 1; color: var(--silver-light); }
  .exp-label { left: 813px; top: 477px; font-size: 49px; font-weight: 400; line-height: 1; color: var(--silver-light); }
  .exp-field { left: 817px; top: 553px; font-size: 34px; font-weight: 800; line-height: 35px; color: var(--gold); letter-spacing: 0.5px; }
  .exp-portfolio { left: 818px; top: 702px; font-size: 27px; font-weight: 500; line-height: 31px; color: var(--silver-light); letter-spacing: 0.5px; }

  .location-label { right: 72px; top: 833px; font-size: 24px; font-weight: 600; letter-spacing: 5px; color: var(--text-dark); line-height: 1; }
  .location-value { right: 72px; top: 867px; font-size: 38px; font-weight: 700; color: var(--white); line-height: 1; }

  .requirements { position: absolute; left: 95px; top: 636px; list-style: none; }
  .requirement { position: relative; padding-left: 28px; height: 74.5px; }
  .requirement svg { position: absolute; left: -8px; top: 7px; width: 17px; height: 17px; }
  .requirement-title { font-size: 21.5px; font-weight: 700; color: var(--gold); line-height: 24px; }
  .requirement-detail { font-size: 17.5px; font-weight: 500; color: var(--text-dark); line-height: 22px; }

  .tagline { left: 83px; top: 1052px; font-size: 26px; font-style: italic; font-weight: 500; color: var(--silver-light); letter-spacing: 2px; line-height: 1; }
  .tagline b { font-weight: 700; color: var(--gold); }
  .website { left: 84px; top: 1107px; font-size: 34px; font-weight: 700; color: var(--silver-light); line-height: 1; }
  .website span { color: var(--gold); }

  .apply { right: 65px; top: 966px; font-size: 71px; font-weight: 700; color: var(--silver); line-height: 1; letter-spacing: -0.5px; }
  .apply-note { right: 65px; top: 1055px; font-size: 26px; font-weight: 500; color: var(--gold); line-height: 1; }
  .handle { right: 72px; top: 1106px; font-size: 28px; font-weight: 700; color: var(--silver-light); line-height: 1; display: flex; align-items: center; gap: 14px; }
  .handle-dot { width: 30px; height: 30px; border-radius: 50%; background: var(--gold); }
  .shapes { position: absolute; inset: 0; }
</style>
</head>
<body>
<main class="flyer">
  <div class="blueprint-backdrop" role="img" aria-label="Faint dark architectural floor plan drawing behind the headline"></div>

  <svg class="shapes" width="1200" height="1200" viewBox="0 0 1200 1200" aria-hidden="true">
    <line x1="466" y1="346" x2="1135" y2="346" stroke="var(--rule)" stroke-width="2"/>
    <line x1="817" y1="537" x2="1128" y2="537" stroke="var(--rule)" stroke-width="2"/>
    <line x1="817" y1="684" x2="1128" y2="684" stroke="var(--rule)" stroke-width="2"/>
    <path d="M0 595 H718 Q740 595 736 616 L664 995 Q659 1019 636 1019 H0 Z" fill="var(--silver)"/>
    <path d="M720 821 H1200 V929 H716 Q699 929 703 912 L716 838 Q719 821 736 821 Z" fill="var(--gold-band)"/>
    <g stroke="var(--panel-rule)" stroke-width="1.5">
      <line x1="123" y1="697" x2="697" y2="697"/>
      <line x1="123" y1="773" x2="679" y2="773"/>
      <line x1="123" y1="845" x2="668" y2="845"/>
      <line x1="123" y1="920" x2="654" y2="920"/>
    </g>
  </svg>

  <h1 class="abs headline-hiring">Hiring</h1>
  <div class="abs headline-were">WE’RE</div>
  <div class="abs role-kicker">CONSTRUCTION</div>
  <h2 class="abs role-title">PROJECT<br>MANAGER</h2>

  <div class="abs brand">
    <div class="brand-name">VELSTRIDE</div>
    <div class="brand-sub">builders</div>
  </div>

  <div class="abs exp-number">5+</div>
  <div class="abs exp-years">YEARS</div>
  <div class="abs exp-label">EXPERIENCE</div>
  <div class="abs exp-field">IN RESIDENTIAL<br>PROJECT<br>MANAGEMENT</div>
  <div class="abs exp-portfolio">with a strong portfolio<br>of completed homes</div>

  <div class="abs location-label">LOCATION</div>
  <div class="abs location-value">Bergen County, NJ</div>

  <ul class="requirements">
    <li class="requirement">
      <svg viewBox="0 0 20 20"><circle cx="10" cy="10" r="8.5" fill="none" stroke="var(--text-dark)" stroke-width="1.6"/><path d="M6 10.2l2.7 2.6L14 7.6" fill="none" stroke="var(--text-dark)" stroke-width="1.6"/></svg>
      <div class="requirement-title">Excellent leadership skills</div>
      <div class="requirement-detail">leads teams with confidence and clarity</div>
    </li>
    <li class="requirement">
      <svg viewBox="0 0 20 20"><circle cx="10" cy="10" r="8.5" fill="none" stroke="var(--text-dark)" stroke-width="1.6"/><path d="M6 10.2l2.7 2.6L14 7.6" fill="none" stroke="var(--text-dark)" stroke-width="1.6"/></svg>
      <div class="requirement-title">Communicates seamlessly</div>
      <div class="requirement-detail">with architects, engineers, designers and clients</div>
    </li>
    <li class="requirement">
      <svg viewBox="0 0 20 20"><circle cx="10" cy="10" r="8.5" fill="none" stroke="var(--text-dark)" stroke-width="1.6"/><path d="M6 10.2l2.7 2.6L14 7.6" fill="none" stroke="var(--text-dark)" stroke-width="1.6"/></svg>
      <div class="requirement-title">Knows how to manage</div>
      <div class="requirement-detail">budgets and timelines without compromising quality</div>
    </li>
    <li class="requirement">
      <svg viewBox="0 0 20 20"><circle cx="10" cy="10" r="8.5" fill="none" stroke="var(--text-dark)" stroke-width="1.6"/><path d="M6 10.2l2.7 2.6L14 7.6" fill="none" stroke="var(--text-dark)" stroke-width="1.6"/></svg>
      <div class="requirement-title">Solves problems</div>
      <div class="requirement-detail">with a positive solution first mindset</div>
    </li>
    <li class="requirement">
      <svg viewBox="0 0 20 20"><circle cx="10" cy="10" r="8.5" fill="none" stroke="var(--text-dark)" stroke-width="1.6"/><path d="M6 10.2l2.7 2.6L14 7.6" fill="none" stroke="var(--text-dark)" stroke-width="1.6"/></svg>
      <div class="requirement-title">Pays attention to every detail</div>
      <div class="requirement-detail">because in luxury the small things are the big things</div>
    </li>
  </ul>

  <div class="abs tagline">Build <b>Luxury</b>. Lead <b>Excellence</b>.</div>
  <div class="abs website"><span>www.</span>velstridebuilders<span>.com</span></div>

  <div class="abs apply">Apply Now</div>
  <div class="abs apply-note">Link in Bio or DM to connect.</div>
  <div class="abs handle"><span class="handle-dot"></span>velstridebuilders</div>
</main>
</body>
</html>
```